Medical Practice and Business Coaching Website Design

I need a professional website designed for a medical business, TQP Medical.
The website will be hosted on Vorluna (similar design functionality as ZEPT).

About the website:
Pages for the website:
- Home page (a brief overview of the company with a section for "Ultrasound Clinics" and "Coaching and Courses" that link to these pages with all the info and packages for these sections)
- About Us (section for company info and info about Delphine Ashcombe, founder and business coach)
- Ultrasound Clinics (all the info about ultrasound, our packages, links to book, gallery of 3D/4D images, FAQs, social media links)
- Coaching and Courses (All of our coaching package info, course info with a waiting list sign up, section for free business download resources, social media links, blog posts)
- Contact Us (info for our harrowgate ultrasound location and bookings with a map, contact form, email and phone details)

Pages that are also needed but not visible in the top menu:
- Blog Page
- Waiting List Page x2 (Dubbo pop-up 3D clinic, Online Course)
- Thanks for subscribing page

We have a company logo and a logo for both the ultrasound clinics and the Coaching sides of the business. They are attached as well as the HEX codes for the branding colours. Ideally the company areas of the site will be in the blue, purple and teal colours. The ultrasound clinics page will be mostly in the purple with the "clinics" logo featuring on the page.
The courses and coaching page will be dominant in the blue branding colours with accents of purple and teal. The courses logo will be somewhere on the page too.

About our company:
Our company has 2 separate businesses which will have their own pages on the website.
We have a medical imaging business which specialises in ultrasound. We have 3 locations/services:
- Harrowgate Ultrasound: open Fridays and the occasional saturday. Our main focus and where the focus on the clinical page needs to be.
- East Corrimbal Ultrasound: Currently closed, no re-opening date and unlikely to reopen.
- Pop-up clinics: most commonly occur in Dubbo. occasionally in Parkes. Dates for next pop-up will be announced in the future.

Our Harrowgate practice offers both diagnostic ultrasound (referral from doctor) for all areas of the body and 3d/4d pregnancy ultrasounds for entertainment purposes.
The content for the ultrasound clinics part of the website can be found on the current harrowgate ultrasound website: harrowgateultrasound.com.au
This website will be replaced by the new company site. All of the info on this site will end up on the clinics page of the new company website.

The second part of the company is a coaching and courses service for medical professionals who want to start or grow their business.
We currently have coaching packages for 1-on-1 online advice and guidance.

Coaching: all take place on Zoom and can be recorded for them to watch again after. Notes, documents and links that are discussed are provided after session

- FREE 15 minute session: discuss current business or business idea, if and how I can help and potential things they can do. One per client

- Single Coaching Session - 1hr with Delphine

- Silver coaching package: 1 x 1hr Coaching Call with Delphine
Unlimited Email with Delphine for 1 month
Access to our Private Facebook Group to network with other medical professionals and business owners

- Silver Coaching Package With Social Media Management:
As above with 1 month Social Media Management (15 posts, Facebook and Instagram)

- Gold coaching package: 2 x 1hr Coaching Calls with Delphine
Access to our Private Facebook

- Gold Coaching Package With Social Media Management:

- Business Sidekick Package: Unlimited Coaching Calls
Unlimited SMS
Unlimited Emails
Social Media Management (Facebook and Instagram, 1 post per day) Valued at over $700
Business Masterclass (something different each month...social media, medicare, website, branding, live events, etc)

Enrollment for our first course opens in May and clients can join the waitlist in the meantime.
Course is aimed at medical professionals who want to grow their patient numbers and create an online presence for their business.
Ideal for: small practices where the owner does everything, not necessarily familiar with marketing/social media/websites, goes to the very basics and steps through everything in getting a logo, branding, website, building social media pages, creating content.

Course name to come but it will be something like "helpful marketing in healthcare" or "the business of healthcare"

We will also have a blog on the website and a podcast (in the future).

I would like a testimonial on at least the clinics page and the coaching page. Here is one for each but I have more if need be:
Coaching: "I knew I wanted to start my own business but I had no idea where to begin. It would have been easy to abort my dreams of starting my own business had it not been for the direction and unwavering support of Delphine from TQP medical. Delphine dissected the process into manageable bit sized pieces for me and worked tirelessly behind the scenes ensuring everything was on track. Her friendly, warm and approachable manner
equated to more than her just being my business coach, she has now become a friend.
Thank you!!"

Ultrasound testimonial: "Amazing service! Best ultrasound experience I’ve had. Super friendly and informative staff. Great technology. If I didn’t live so far away I’d go to Harrowgate for all my ultrasounds!"

I would also like a section for a welcome video (yet to be recorded) on the home page, ultrasound clinics page and coaching/courses page.

I've attached the company logo and the sub-logos in different formats. There is also a head shot of Delphine for the about us page, an image of Delphine with a coaching client for the coaching page and multiple 3D ultrasound images for the gallery on the clinics page.

Target Market(s)

Mostly targeted at medical professionals. Pregnant women and anyone needing an ultrasound are the targets for the clinics page

Industry/Entity Type

Healthcare

Number of Pages Required

5+ page

Colors
0054AA
0677BA
7BADD7
CADEEF
E8F1F8
0094D4
00A9DD
6FCCEA
C7EBF8
E9F6FB
00AB8E
00BBA5
67D7C9
C6EFE9
E9F9F6
A7469A
B969AE
D3A5CF
EDDBEB
F8F0F9
6B429C
8869AF
B7A5CE
E3DAEB
F3F0F8

```html
<!DOCTYPE html>
<html lang="en">
<head>
<meta charset="utf-8">
<title>TQP Clinics — Home</title>
<link rel="stylesheet" href="https://fonts.googleapis.com/css2?family=Libre+Baskerville:wght@700&family=Roboto:wght@400;500;700&display=swap">
<style>
:root{
  --purple-deep:#563593;
  --purple-rich:#8a3b95;
  --purple-head:#5a3a96;
  --purple-accent:#8c3a8f;
  --ink:#333;
  --text:#555;
  --muted:#777;
  --soft-bg:#f1f2f5;
  --footer-bg:#f2f2f4;
  --white:#fff;
  --grad:linear-gradient(100deg,var(--purple-deep) 0%,var(--purple-rich) 100%);
}
*{box-sizing:border-box;margin:0;padding:0}
html,body{width:1200px;height:3315px;overflow:hidden}
body{position:relative;font-family:"Roboto",Arial,sans-serif;color:var(--text);background:var(--white)}
.abs{position:absolute}
.serif{font-family:"Libre Baskerville",Georgia,serif;font-weight:700;text-transform:uppercase;letter-spacing:1px}

/* header */
.site-header{left:0;top:0;width:1200px;height:103px;background:var(--white);z-index:3}
.header-disc{left:63px;top:0;width:194px;height:171px;border-radius:0 0 97px 97px;background:var(--white);z-index:4}
.brand-name{left:63px;top:72px;width:194px;text-align:center;font-size:20px;font-weight:500;color:var(--purple-accent);z-index:5}
.main-nav{right:111px;top:44px;display:flex;gap:29px;font-size:14px;font-weight:500;color:#333;z-index:5}
.main-nav .active{color:var(--purple-accent)}

/* hero */
.hero{left:0;top:103px;width:1200px;height:599px;background:var(--grad)}
.hero-title{left:112px;top:274px;color:var(--white);font-size:37px;line-height:52px}
.hero-lead{left:112px;top:384px;width:360px;color:var(--white);font-size:20px;line-height:30px}
.btn-video{left:112px;top:472px;width:145px;height:51px;background:var(--white);color:var(--purple-accent);font-size:13px;font-weight:700;display:flex;align-items:center;justify-content:center;gap:6px;border-radius:2px}
.hero-photo{left:601px;top:158px;width:487px;height:488px;background:linear-gradient(135deg,#e9e7e4,#cfc9c4 55%,#b07a5e)}
.slide-arrow{top:383px;width:38px;height:38px;background:var(--white);border-radius:3px;display:flex;align-items:center;justify-content:center}

/* about */
.about-frame{left:112px;top:813px;width:444px;height:443px;border:3px solid var(--purple-accent)}
.about-photo{left:129px;top:795px;width:445px;height:444px;background:linear-gradient(160deg,#9a9a9a,#5e5e5e 60%,#2e2e2e)}
.about-title{left:636px;top:836px;font-size:33px;color:var(--purple-head)}
.about-copy{left:636px;top:894px;width:453px;font-size:14px;line-height:25.7px;text-align:justify;color:var(--text)}
.about-copy p+p{margin-top:13px}
.btn{height:51px;background:var(--grad);color:var(--white);font-size:14px;font-weight:700;display:flex;align-items:center;justify-content:center;border-radius:3px}
.about-btn{left:636px;top:1143px;width:137px}
.dots{left:570px;top:1291px;display:flex;align-items:center;gap:14px}
.dots i{display:block;width:5px;height:5px;border-radius:50%;background:var(--purple-accent)}
.dots b{display:block;width:19px;height:19px;border-radius:50%;border:2px solid var(--purple-accent);position:relative}
.dots b::after{content:"";position:absolute;left:4px;top:4px;width:7px;height:7px;border-radius:50%;background:var(--purple-accent)}

/* courses */
.courses{left:0;top:1383px;width:1200px;height:341px;background:var(--soft-bg)}
.section-title{left:0;width:1200px;text-align:center;font-size:33px;color:var(--purple-head)}
.courses-lead{left:200px;top:1509px;width:800px;text-align:center;font-size:17px;line-height:28px;color:#444}
.courses-btn{left:509px;top:1600px;width:182px}

/* coaching */
.coach-card{top:1889px;width:231px}
.coach-img{width:231px;height:162px}
.coach-price{margin-top:17px;font-size:17px;font-weight:500;color:var(--purple-accent)}
.coach-name{margin-top:8px;font-size:17px;font-weight:500;color:#333}
.coach-meta{margin-top:8px;font-size:12.5px;color:#555;display:flex;align-items:center;gap:8px}
.coach-btn{left:509px;top:2186px;width:182px}

/* community */
.community{left:0;top:2312px;width:1200px;height:197px;background:var(--grad)}
.community-title{left:112px;top:2364px;color:var(--white);font-size:32px;line-height:48px}
.plane{left:380px;top:2366px}
.field{top:2390px;width:258px;height:35px;border-bottom:1px solid rgba(255,255,255,.75);color:var(--white);font-size:15px}
.send{left:1072px;top:2394px}

/* testimonials */
.t-card{top:2680px;width:313px;height:243px;background:var(--white);box-shadow:0 4px 20px rgba(0,0,0,.1);padding:22px 24px}
.t-place{font-size:18px;font-weight:500;color:var(--purple-accent)}
.t-quote{position:absolute;right:24px;top:26px;display:flex;gap:6px}
.t-quote span{width:30px;height:38px;border-radius:8px 8px 2px 14px;background:#eeeef1}
.t-text{margin-top:16px;font-size:12.6px;line-height:23px;color:#666}
.t-person{margin-top:16px;display:flex;align-items:center;gap:14px}
.t-avatar{width:52px;height:52px;border-radius:50%;background:linear-gradient(135deg,#d8b79c,#8a6a55)}
.t-name{font-size:15px;font-weight:500;color:var(--purple-accent)}
.t-town{font-size:14px;color:#444;margin-top:2px}

/* footer */
.site-footer{left:0;top:3017px;width:1200px;height:298px;background:var(--footer-bg)}
.f-head{top:3063px;font-size:18px;font-weight:500;color:#333}
.f-list{top:3103px;font-size:14.5px;line-height:29px;color:#444;list-style:none}
.f-contact{left:112px;top:3103px;font-size:14.5px;line-height:22px;color:#444}
.f-row{display:flex;gap:16px;align-items:flex-start}
.f-social{left:112px;top:3206px;display:flex;gap:16px}
.f-social span{width:16px;height:16px;border-radius:50%;border:2px solid #444}
.f-rule{left:112px;top:3264px;width:976px;height:1px;background:#d4d4d8}
.copyright{left:0;top:3280px;width:1200px;text-align:center;font-size:13px;color:#444}
.copyright b{font-weight:700;color:#333}
</style>
</head>
<body>

<header class="abs site-header"></header>
<div class="abs header-disc"></div>
<div class="abs brand-name">TQP CLINICS</div>
<nav class="abs main-nav">
  <span class="active">HOME</span><span>ABOUT US</span><span>ULTRASOUND CLINICS</span><span>COACHING AND COURSES</span><span>CONTACT US</span>
</nav>

<section class="abs hero"></section>
<h1 class="abs serif hero-title">Welcome to TQP<br>Clinics</h1>
<p class="abs hero-lead">We have a medical imaging business which specialises in ultrasound.</p>
<a class="abs btn-video">
  <svg width="13" height="13" viewBox="0 0 14 14"><circle cx="7" cy="7" r="6" fill="none" stroke="currentColor" stroke-width="1.5"/><path d="M5.5 4.5 9.5 7 5.5 9.5Z" fill="currentColor"/></svg>WATCH VIDEO</a>
<div class="abs hero-photo" role="img" aria-label="Photo of two women in an ultrasound room beside an ultrasound machine"></div>
<div class="abs slide-arrow" style="left:38px"><svg width="12" height="12" viewBox="0 0 12 12"><path d="M8 1 3 6l5 5" fill="none" stroke="#8c3a8f" stroke-width="2"/></svg></div>
<div class="abs slide-arrow" style="left:1125px"><svg width="12" height="12" viewBox="0 0 12 12"><path d="M4 1l5 5-5 5" fill="none" stroke="#8c3a8f" stroke-width="2"/></svg></div>

<div class="abs about-frame"></div>
<div class="abs about-photo" role="img" aria-label="Black and white portrait of the founder"></div>
<h2 class="abs serif about-title">About Us</h2>
<div class="abs about-copy">
  <p>Lorem ipsum dolor sit amet, consectetur adipiscing elit, sed do eiusm od tempor incididunt ut labore et dolore magna aliqua. Ut enim ad minim veniam, quis nostrud exercitation ullamco laboris nisi ut aliquip ex ea commodo consequat.</p>
  <p>Lorem ipsum dolor sit amet, consectetur adipiscing elit, sed do eiusm od tempor incididunt ut labore et dolore magna aliqua. Ut enim ad minim veniam, quis nostrud exercita.Duis aute irure dolor in repreh enderit in voluptate velit essea.</p>
</div>
<a class="abs btn about-btn">LEARN MORE</a>
<div class="abs dots"><i></i><b></b><i></i></div>

<section class="abs courses"></section>
<h2 class="abs serif section-title" style="top:1447px">Our Courses</h2>
<p class="abs courses-lead">FREE 15 minute session: discuss current business or business idea, if and how I can help and potential things they can do. One per client</p>
<a class="abs btn courses-btn">START FREE COURSE</a>

<h2 class="abs serif section-title" style="top:1811px">Coaching</h2>
<div class="abs coach-card" style="left:112px">
  <div class="coach-img" role="img" aria-label="3D ultrasound image of a baby" style="background:radial-gradient(circle at 45% 45%,#d9a57c,#8a5a3c 45%,#0a0a0a 75%)"></div>
  <div class="coach-price">$120</div><div class="coach-name">Single Coaching Session</div>
  <div class="coach-meta"><svg width="11" height="11" viewBox="0 0 12 12"><circle cx="6" cy="6" r="5" fill="none" stroke="#8c3a8f" stroke-width="1.4"/><path d="M6 3.5V6h2" stroke="#8c3a8f" fill="none"/></svg>1hr with Delphine</div>
</div>
<div class="abs coach-card" style="left:360px">
  <div class="coach-img" role="img" aria-label="3D ultrasound image of a baby" style="background:linear-gradient(135deg,#c98c62,#e2b08a 50%,#9a6442)"></div>
  <div class="coach-price">$220</div><div class="coach-name">Silver coaching package</div>
  <div class="coach-meta"><svg width="11" height="11" viewBox="0 0 12 12"><circle cx="6" cy="6" r="5" fill="none" stroke="#8c3a8f" stroke-width="1.4"/><path d="M6 3.5V6h2" stroke="#8c3a8f" fill="none"/></svg>1 x 1hr Coaching Call with Delphine</div>
</div>
<div class="abs coach-card" style="left:608px">
  <div class="coach-img" role="img" aria-label="3D ultrasound image of a baby" style="background:radial-gradient(ellipse at 50% 50%,#d29a6e,#7a4a30 40%,#050505 70%)"></div>
  <div class="coach-price">$300</div><div class="coach-name">Gold coaching package</div>
  <div class="coach-meta"><svg width="11" height="11" viewBox="0 0 12 12"><circle cx="6" cy="6" r="5" fill="none" stroke="#8c3a8f" stroke-width="1.4"/><path d="M6 3.5V6h2" stroke="#8c3a8f" fill="none"/></svg>2 x 1hr Coaching Calls with Delphine</div>
</div>
<div class="abs coach-card" style="left:857px">
  <div class="coach-img" role="img" aria-label="3D ultrasound image of a baby" style="background:linear-gradient(135deg,#e0ad85,#c8875c 55%,#a36a46)"></div>
  <div class="coach-price">$700</div><div class="coach-name">Business Sidekick Package</div>
  <div class="coach-meta"><svg width="11" height="11" viewBox="0 0 12 12"><circle cx="6" cy="6" r="5" fill="none" stroke="#8c3a8f" stroke-width="1.4"/><path d="M6 3.5V6h2" stroke="#8c3a8f" fill="none"/></svg>Unlimited Coaching Calls</div>
</div>
<a class="abs btn coach-btn">VIEW ALL COACHING</a>

<section class="abs community"></section>
<h2 class="abs serif community-title">Join Our<br>Community</h2>
<svg class="abs plane" width="90" height="88" viewBox="0 0 90 88"><path d="M86 3 4 44l26 10 6 30 14-20 20 14Z M30 54 86 3 50 64" fill="none" stroke="rgba(255,255,255,.25)" stroke-width="5" stroke-linejoin="round"/></svg>
<div class="abs field" style="left:525px">Email</div>
<div class="abs field" style="left:799px">Name</div>
<svg class="abs send" width="16" height="12" viewBox="0 0 16 12"><path d="M0 6h13M9 2l4 4-4 4" fill="none" stroke="#fff" stroke-width="2"/></svg>

<h2 class="abs serif section-title" style="top:2598px">Testimonials</h2>
<article class="abs t-card" style="left:112px">
  <div class="t-place">Harrowgate Ultrasound</div><div class="t-quote"><span></span><span></span></div>
  <p class="t-text">Amazing service! Best ultrasound experience I’ve had. Super friendly and informative staff. Great technology. If I didn’t live so far away I’d go to Harrowgate for all my ultrasounds!</p>
  <div class="t-person"><div class="t-avatar" role="img" aria-label="Client portrait"></div><div><div class="t-name">Maren Holt</div><div class="t-town">Harrowgate</div></div></div>
</article>
<article class="abs t-card" style="left:443px">
  <div class="t-place">Harrowgate Ultrasound</div><div class="t-quote"><span></span><span></span></div>
  <p class="t-text">Amazing service! Best ultrasound experience I’ve had. Super friendly and informative staff. Great technology. If I didn’t live so far away I’d go to Harrowgate for all my ultrasounds!</p>
  <div class="t-person"><div class="t-avatar" role="img" aria-label="Client portrait" style="background:linear-gradient(135deg,#e6e6e6,#9c8f86)"></div><div><div class="t-name">Maren Holt</div><div class="t-town">Harrowgate</div></div></div>
</article>
<article class="abs t-card" style="left:774px">
  <div class="t-place">Harrowgate Ultrasound</div><div class="t-quote"><span></span><span></span></div>
  <p class="t-text">Amazing service! Best ultrasound experience I’ve had. Super friendly and informative staff. Great technology. If I didn’t live so far away I’d go to Harrowgate for all my ultrasounds!</p>
  <div class="t-person"><div class="t-avatar" role="img" aria-label="Client portrait" style="background:linear-gradient(135deg,#7c8a6a,#c79a7a)"></div><div><div class="t-name">Maren Holt</div><div class="t-town">Harrowgate</div></div></div>
</article>

<footer class="abs site-footer"></footer>
<h3 class="abs f-head" style="left:112px">CONNECT</h3>
<div class="abs f-contact">
  <div class="f-row"><svg width="9" height="13" viewBox="0 0 10 14" style="margin-top:4px"><path d="M5 0a5 5 0 0 0-5 5c0 4 5 9 5 9s5-5 5-9a5 5 0 0 0-5-5Zm0 7a2 2 0 1 1 0-4 2 2 0 0 1 0 4Z" fill="#8c3a8f"/></svg><span>465 Lorum Ipsum Dolore Sit,<br>Harrowgate Ultrasound</span></div>
  <div class="f-row" style="margin-top:14px"><svg width="12" height="12" viewBox="0 0 12 12" style="margin-top:4px"><path d="M2.5 0 5 3 3.6 4.6a8 8 0 0 0 3.8 3.8L9 7l3 2.5L10.5 12C5 11.5.5 7 0 1.5Z" fill="#8c3a8f"/></svg><span>+1 (555) 010 4821</span></div>
</div>
<div class="abs f-social" aria-label="Social media links"><span></span><span></span></div>
<h3 class="abs f-head" style="left:580px">EXPLORE</h3>
<ul class="abs f-list" style="left:580px"><li>Courses</li><li>Blog</li><li>Waiting List</li><li>Terms Of Use</li><li>Privacy</li></ul>
<h3 class="abs f-head" style="left:958px">RESOURCES</h3>
<ul class="abs f-list" style="left:958px"><li>Home</li><li>About Us</li><li>Ultrasound Clinics</li><li>Coaching &amp; Courses</li><li>Contact Us</li></ul>
<div class="abs f-rule"></div>
<p class="abs copyright">© 2022 <b>TQP CLINICS</b> &nbsp;|&nbsp; All Rights Reserved</p>

</body>
</html>
```